Meadowlark Property Review is a leading provider of residential appraisal and home inspection products in S

I need a business card/logo designed that obviously describes my business. We are a residential appraisal and home inspection company in Springfield, MO. We offer residential appraisals, home inspection, pest inspection and radon gas measurement. We have been in business for 18 years and hold state certified residential appraisal licenses and OBREX certified home inspection licenses. I have a logo that I really like and will attach, but would be open to new suggestions. I like more modern designs than traditional and would like a two sided card with our services, licenses and qualifications on the back.

```html
<!DOCTYPE html>
<html lang="en">
<head>
<meta charset="utf-8">
<title>Meadowlark Property Review — Business Card</title>
<link rel="stylesheet" href="https://fonts.googleapis.com/css2?family=Open+Sans:wght@400;600;700&display=swap">
<style>
  :root {
    --page: #e9e6e1;
    --card-white: #ffffff;
    --card-black: #0c0c0c;
    --ink: #1e1e1e;
    --gold: #c9a15e;
    --gold-dark: #9a7b4f;
    --orange: #f07a1c;
    --badge: #d8c24a;
    --badge-ribbon: #9c1f2c;
    --muted: #d6d6d6;
  }
  * { box-sizing: border-box; margin: 0; padding: 0; }
  html, body { width: 1200px; height: 913px; overflow: hidden; }
  body {
    background: var(--page);
    font-family: "Open Sans", Arial, sans-serif;
    display: flex;
    align-items: center;
    justify-content: center;
    gap: 36px;
  }
  .card {
    position: relative;
    width: 546px;
    height: 312px;
    border-radius: 4px;
    box-shadow: 0 6px 18px rgba(0,0,0,.18);
    overflow: hidden;
  }
  .card--front { background: var(--card-white); color: var(--ink); }
  .card--back { background: var(--card-black); color: #fff; }

  .wordmark {
    font-weight: 700;
    color: var(--gold);
    font-size: 24px;
    line-height: 1.05;
    letter-spacing: .2px;
  }
  .card--front .wordmark {
    position: absolute;
    top: 30px;
    right: 30px;
    width: 230px;
    text-align: left;
  }
  .rule {
    position: absolute;
    height: 1.5px;
    background: var(--gold-dark);
  }
  .card--front .rule { top: 92px; right: 30px; width: 250px; }
  .address {
    position: absolute;
    top: 102px;
    right: 30px;
    width: 250px;
    font-size: 12.5px;
    font-weight: 600;
    line-height: 1.45;
  }
  .badge {
    position: absolute;
    top: 118px;
    left: 30px;
    width: 52px;
    height: 52px;
  }
  .identity {
    position: absolute;
    left: 30px;
    top: 190px;
  }
  .identity__name {
    font-size: 19px;
    font-weight: 700;
    letter-spacing: .4px;
  }
  .identity__role {
    font-size: 12px;
    font-weight: 600;
    color: var(--gold);
    border-bottom: 1.5px solid var(--gold);
    display: inline-block;
    padding-bottom: 1px;
    width: 90px;
  }
  .contacts {
    position: absolute;
    left: 30px;
    top: 240px;
    list-style: none;
    font-size: 12.5px;
    font-weight: 600;
    line-height: 16px;
  }
  .contacts li { display: flex; align-items: center; gap: 8px; }
  .contacts svg { width: 11px; height: 11px; flex: none; }

  .card--back .wordmark {
    position: absolute;
    top: 40px;
    left: 0;
    width: 100%;
    text-align: center;
    font-size: 27px;
  }
  .card--back .rule {
    top: 108px;
    left: 150px;
    width: 246px;
    background: var(--gold);
  }
  .services {
    position: absolute;
    left: 40px;
    top: 132px;
    list-style: none;
    font-size: 13.5px;
    line-height: 18px;
    font-weight: 400;
    letter-spacing: .3px;
  }
  .services li { display: flex; align-items: center; gap: 9px; }
  .services li::before {
    content: "";
    width: 9px;
    height: 9px;
    border-radius: 50%;
    background: var(--orange);
  }
  .tagline {
    position: absolute;
    left: 40px;
    right: 40px;
    top: 254px;
    font-size: 10px;
    line-height: 1.45;
    color: var(--muted);
  }
</style>
</head>
<body>

  <section class="card card--front" aria-label="Business card front">
    <div class="wordmark">Meadowlark Property Review</div>
    <div class="rule"></div>
    <p class="address">Meadowlark Property Review 480 Linden Avenue Suite C Springfield, MO 65800</p>

    <svg class="badge" viewBox="0 0 52 52" role="img" aria-label="Certification badge">
      <circle cx="26" cy="26" r="24" fill="var(--badge)"/>
    </svg>

    <div class="identity">
      <div class="identity__name">DANA WHITFIELD</div>
      <div class="identity__role">OWNER</div>
    </div>

    <ul class="contacts">
      <li>
        <svg viewBox="0 0 12 12" aria-hidden="true"><path d="M2 1l2 0 1 3-1.3 1a7 7 0 0 0 3.3 3.3L8 7l3 1v2c0 .6-.4 1-1 1A9 9 0 0 1 1 2c0-.6.4-1 1-1z" fill="var(--ink)"/></svg>
        417-555-0142
      </li>
      <li>
        <svg viewBox="0 0 12 12" aria-hidden="true"><rect x="3" y="0.5" width="6" height="11" rx="1.2" fill="var(--ink)"/><rect x="4" y="2" width="4" height="6.5" fill="#fff"/></svg>
        417-555-0187
      </li>
      <li>
        <svg viewBox="0 0 12 12" aria-hidden="true"><rect x="0.8" y="2.3" width="10.4" height="7.4" fill="none" stroke="var(--ink)" stroke-width="1.2"/><path d="M1 2.6l5 4 5-4" fill="none" stroke="var(--ink)" stroke-width="1.2"/></svg>
        info@meadowlarkreview.com
      </li>
      <li>
        <svg viewBox="0 0 12 12" aria-hidden="true"><circle cx="6" cy="6" r="5" fill="none" stroke="var(--ink)" stroke-width="1.1"/><ellipse cx="6" cy="6" rx="2.2" ry="5" fill="none" stroke="var(--ink)" stroke-width="1"/><path d="M1 6h10" stroke="var(--ink)" stroke-width="1"/></svg>
        www.meadowlarkreview.com
      </li>
    </ul>
  </section>

  <section class="card card--back" aria-label="Business card back">
    <div class="wordmark">Meadowlark Property Review</div>
    <div class="rule"></div>
    <ul class="services">
      <li>APPRAISAL</li>
      <li>HOME INSPECTION</li>
      <li>TERMITE</li>
      <li>RADON</li>
      <li>WELL &amp; SEPTIC INSPECTION</li>
      <li>ENERGY AUDITS</li>
    </ul>
    <p class="tagline">With years of experience behind us, we’re prepared to tackle anything from a first time buyer’s starter home or a seasoned buyer purchasing a luxurious dream home.</p>
  </section>

</body>
</html>
```